Slide Master for Holloway Engines - A Systematic Hedge Fund

We are looking for someone to produce a theme and slide master for us for our investor presentations. I have uploaded a few examples of templates that we would like to have included:
Main Title
Section Title
Slides with just bullet points
Different image/table configurations with bullet points and foot notes
Biographies of different lengths
A disclaimer (no one will read this but it should still look nice and needs to be in the presentations)
I have also uploaded the company logo, business card and colour definitions. Currently we have a blue colour scheme defined, but it would be nice to get a complementary set of colours so that when we have charts with more elements we can just draw from those.
The most important thing is that the slide master must be of general use to us. We arn't looking to have a specific presentation designed for us, but a theme/style that we can apply ourselves to any presentation we need to give in the future. It should have clearly defined guidelines for where content should go (and if this is different with and without footnotes for example). We would also like it to have a similar feel to the logo/business cards, so matt colours, high contrast, but not busy.
I'm excited to see the results!

```html
<!DOCTYPE html>
<html lang="en">
<head>
<meta charset="utf-8">
<title>Holloway Engines – Slide Master</title>
<link href="https://fonts.googleapis.com/css2?family=Roboto:wght@100;300;400;500;700;900&display=swap" rel="stylesheet">
<style>
  :root {
    --navy: #0c3c6e;
    --navy-deep: #062f5c;
    --blue: #4f8ad3;
    --band-a: #3b72c0;
    --band-b: #5c97dd;
    --paper-hi: #fdfdfd;
    --paper-lo: #dcdcdc;
    --ink: #1d2a3a;
    --accent: #b04aa8;
    --line: #7fa6d6;
  }
  * { box-sizing: border-box; margin: 0; padding: 0; }
  html, body { width: 1200px; height: 1200px; overflow: hidden; }
  body {
    background: linear-gradient(180deg, #f6f6f6, #ececec);
    font-family: 'Roboto', Arial, sans-serif;
    color: var(--ink);
    position: relative;
  }
  .slide {
    position: absolute;
    width: 608px; height: 342px;
    transform-origin: 0 0;
    transform: scale(0.6205);
    overflow: hidden;
    background: radial-gradient(ellipse at 60% 35%, var(--paper-hi) 0%, #efefef 55%, var(--paper-lo) 100%);
  }
  .slide > * { position: absolute; }
  .cover {
    position: absolute; left: 40px; top: 50px;
    width: 1148px; height: 644px;
    transform-origin: 0 0; transform: scale(0.6211);
    background: radial-gradient(ellipse at 50% 40%, #ffffff 0%, #efefef 55%, #d6d6d6 100%);
  }
  .cover-brand { position: absolute; left: 0; right: 0; top: 170px; text-align: center; color: var(--navy); font-weight: 700; }
  .cover-brand .b1 { font-size: 76px; line-height: 1; letter-spacing: 1px; }
  .cover-brand .b2 { font-size: 34px; letter-spacing: 28px; margin-top: 6px; padding-left: 28px; }
  .cover-mark { position: absolute; left: 544px; top: 110px; width: 60px; height: 60px; border-radius: 50%; background: var(--navy); }
  .cover-title { position: absolute; left: 0; right: 0; top: 330px; text-align: center; color: var(--navy); font-weight: 900; font-size: 64px; line-height: 1.02; }
  .caption { position: absolute; font-weight: 500; font-size: 12px; letter-spacing: 4px; color: #111; }
  .num { position: absolute; font-weight: 700; font-size: 11px; color: #111; }

  .band { left: 0; top: 0; width: 608px; height: 115px; background: linear-gradient(90deg, var(--band-a), var(--band-b) 60%, #4a83cc); }
  .band-title { left: 48px; top: 24px; color: #fff; font-weight: 900; font-size: 27px; line-height: 0.92; }
  .band-title .light { font-weight: 300; }
  .band-sub { left: 48px; top: 83px; color: #fff; font-size: 14px; }
  .brand { text-align: center; font-weight: 700; line-height: 1; }
  .brand .w1 { font-size: 20px; letter-spacing: .5px; }
  .brand .w2 { font-size: 10px; letter-spacing: 6px; margin-top: 3px; padding-left: 6px; }
  .brand .dot { display: block; width: 10px; height: 10px; margin: 0 auto 5px; }
  .brand-light { color: #fff; left: 430px; top: 28px; width: 150px; }
  .brand-light .dot { background: #fff; }
  .brand-dark { color: var(--navy); left: 430px; top: 28px; width: 150px; }
  .brand-dark .dot { background: var(--navy); }

  .sec-num { left: 48px; top: 160px; font-size: 140px; font-weight: 100; color: var(--blue); line-height: 1; letter-spacing: -6px; }
  .sec-title { top: 190px; font-size: 31px; font-weight: 900; color: var(--navy); line-height: .95; }

  .legal { top: 150px; width: 150px; font-size: 6.2px; line-height: 1.5; color: #222; }
  .legal-rule { top: 152px; width: 1px; height: 190px; background: var(--line); }
  .legal-dot { top: 148px; width: 12px; height: 12px; border-radius: 50%; background: var(--navy); }

  .h-body { font-weight: 900; color: var(--navy); font-size: 19px; line-height: .92; }
  .h-body .light { font-weight: 300; }
  .bullets { list-style: none; font-size: 12.5px; line-height: 1.35; color: var(--navy); }
  .bullets li { margin-bottom: 8px; }
  .bullets li::before { content: "•"; margin-right: 6px; }
  .body-copy { font-size: 12.5px; line-height: 1.35; color: var(--navy); }
  .footnote { font-size: 4.6px; line-height: 1.45; color: var(--navy); width: 190px; }
  .footnote b { display: block; font-weight: 500; }
  .divider { width: 1px; background: var(--line); }

  .data-table { left: 48px; top: 126px; width: 322px; border-collapse: collapse; font-size: 4.2px; color: #222; border-bottom: 2px solid var(--navy); }
  .data-table th { background: var(--navy); color: #fff; font-weight: 700; text-align: left; padding: 6px 3px; font-size: 4.6px; }
  .data-table td { padding: 2.6px 3px; border-bottom: .5px solid #cfcfcf; }

  .bar-label { font-size: 7.5px; font-weight: 700; color: var(--navy); }
  .photo { width: 77px; height: 106px; border-radius: 14px; background: var(--blue); }
  .name { font-size: 15.5px; font-weight: 900; color: var(--navy); }
  .role { font-size: 8.5px; color: var(--navy); letter-spacing: .3px; padding-bottom: 4px; border-bottom: 1px solid var(--line); }
  .bio { font-size: 10.5px; line-height: 1.5; color: var(--navy); }
  .full-blue { background: linear-gradient(180deg, var(--band-a), var(--band-b) 70%, #5b97dd); }
</style>
</head>
<body>

<!-- Cover -->
<section class="cover">
  <div class="cover-mark"></div>
  <div class="cover-brand"><div class="b1">HOLLOWAY</div><div class="b2">ENGINES</div></div>
  <h1 class="cover-title">TITLE OF<br>PRESENTATION</h1>
</section>
<div class="caption" style="left:347px;top:468px;">THE COVER</div>

<!-- 1 Disclaimer -->
<section class="slide" style="left:804px;top:19px;">
  <div class="band"></div>
  <div class="band-title" style="top:52px;font-size:27px;">DISCLAIMER</div>
  <div class="brand brand-light"><span class="dot"></span><div class="w1">HOLLOWAY</div><div class="w2">ENGINES</div></div>
  <div class="legal-dot" style="left:48px;"></div><div class="legal-rule" style="left:54px;"></div>
  <div class="legal" style="left:70px;">Lorem ipsum dolor sit amet, consectetur adipiscing elit. Vestibulum lacinia eros eu pharetra mollis. Nullam vulputate purus mi, sed maximus est sodales mollis. Mauris nec vulputate eros. Cras lectus lacus, lacinia eu dapibus ac, tincidunt eu nisi. Suspendisse in volutpat risus. Nunc pharetra porttitor lorem. Vivamus at lectus sit amet lacus dictum tincidunt at vel magna. Donec blandit nulla ac erat condimentum, fringilla feugiat ex porttitor. Proin est odio, suscipit vitae magna at, bibendum tincidunt mi. Aenean</div>
  <div class="legal-dot" style="left:235px;"></div><div class="legal-rule" style="left:241px;"></div>
  <div class="legal" style="left:257px;">Lorem ipsum dolor sit amet, consectetur adipiscing elit. Vestibulum lacinia eros eu pharetra mollis. Nullam vulputate purus mi, sed maximus est sodales mollis. Mauris nec vulputate eros. Cras lectus lacus, lacinia eu dapibus ac, tincidunt eu nisi. Suspendisse in volutpat risus. Nunc pharetra porttitor lorem. Vivamus at lectus sit amet lacus dictum tincidunt at vel magna. Donec blandit nulla ac erat condimentum, fringilla feugiat ex porttitor. Proin est odio, suscipit vitae magna at, bibendum tincidunt mi. Aenean</div>
  <div class="legal-dot" style="left:422px;"></div><div class="legal-rule" style="left:428px;"></div>
  <div class="legal" style="left:444px;">Lorem ipsum dolor sit amet, consectetur adipiscing elit. Vestibulum lacinia eros eu pharetra mollis. Nullam vulputate purus mi, sed maximus est sodales mollis. Mauris nec vulputate eros. Cras lectus lacus, lacinia eu dapibus ac, tincidunt eu nisi. Suspendisse in volutpat risus. Nunc pharetra porttitor lorem. Vivamus at lectus sit amet lacus dictum tincidunt at vel magna. Donec blandit nulla ac erat condimentum, fringilla feugiat ex porttitor. Proin est odio, suscipit vitae magna at, bibendum tincidunt mi. Aenean</div>
</section>
<div class="num" style="left:804px;top:234px;">1</div>

<!-- 2 Section one -->
<section class="slide" style="left:804px;top:256px;">
  <div class="brand brand-dark"><span class="dot"></span><div class="w1">HOLLOWAY</div><div class="w2">ENGINES</div></div>
  <div class="sec-num">01</div>
  <div class="sec-title" style="left:176px;">SECTION<br>ONE<br>TITLE</div>
</section>
<div class="num" style="left:804px;top:471px;">2</div>

<!-- 9 Section three -->
<section class="slide" style="left:11px;top:493px;">
  <div class="brand brand-dark"><span class="dot"></span><div class="w1">HOLLOWAY</div><div class="w2">ENGINES</div></div>
  <div class="sec-num">03</div>
  <div class="sec-title" style="left:190px;">SECTION<br>THREE<br>TITLE</div>
</section>
<div class="num" style="left:11px;top:709px;">9</div>

<!-- 6 Doughnut -->
<section class="slide" style="left:408px;top:493px;">
  <div class="band"></div>
  <div class="band-title">ANOTHER<br>SECTION TITLE</div>
  <div class="band-sub">Subsection With A Footnote*</div>
  <div class="brand brand-light"><span class="dot"></span><div class="w1">HOLLOWAY</div><div class="w2">ENGINES</div></div>
  <div class="h-body" style="left:48px;top:146px;">TITLE <span class="light">OF</span><br>DOUGHNAT<br>CHART</div>
  <div class="body-copy" style="left:48px;top:207px;width:110px;">m dolor sit amet, consectetur adipiscing elitm dolor sit ameta</div>
  <div class="footnote" style="left:48px;top:298px;"><b>FOOTNOTE:</b>Data shown net of fees and based on monthly returns since inception; past performance is not indicative of future results and may vary.</div>
  <svg style="left:174px;top:128px;" width="190" height="190" viewBox="0 0 190 190" role="img" aria-label="Doughnut chart, 79 percent">
    <circle cx="95" cy="95" r="78" fill="none" stroke="var(--navy)" stroke-width="26"/>
    <circle cx="95" cy="95" r="78" fill="none" stroke="var(--accent)" stroke-width="26"
            stroke-dasharray="102.9 490.1" stroke-dashoffset="102.9" transform="rotate(-90 95 95)"/>
    <text x="95" y="114" text-anchor="middle" font-family="Roboto, sans-serif" font-weight="900" font-size="54" fill="var(--navy)">79<tspan font-size="30" dy="-18">%</tspan></text>
  </svg>
  <ul class="bullets" style="left:368px;top:160px;width:210px;">
    <li>Lorem ipsum dolor sit amet, consectetur adipiscing elit</li>
    <li>Lorem ipsum dolor sit amet, consectetur adipiscing elit</li>
    <li>Lorem ipsum dolor sit amet, consectetur adipiscing elit</li>
  </ul>
</section>
<div class="num" style="left:408px;top:706px;">6</div>

<!-- 3 Bullets -->
<section class="slide" style="left:804px;top:493px;">
  <div class="band"></div>
  <div class="band-title">SECTION<br>TITLE</div>
  <div class="band-sub">Subsection Title</div>
  <div class="brand brand-light"><span class="dot"></span><div class="w1">HOLLOWAY</div><div class="w2">ENGINES</div></div>
  <div class="h-body" style="left:48px;top:146px;">A HEADER</div>
  <ul class="bullets" style="left:48px;top:173px;width:215px;">
    <li>Lorem ipsum dolor sit amet, consectetur adipiscing elit</li>
    <li>Lorem ipsum dolor sit amet, consectetur adipiscing elit</li>
    <li>Lorem ipsum dolor sit amet, consectetur adipiscing elit</li>
  </ul>
  <div class="divider" style="left:305px;top:140px;height:152px;"></div>
  <div class="h-body" style="left:323px;top:146px;">SECOND HEADER</div>
  <ul class="bullets" style="left:323px;top:173px;width:215px;">
    <li>Lorem ipsum dolor sit amet, consectetur adipiscing elit</li>
    <li>Lorem ipsum dolor sit amet, consectetur adipiscing elit</li>
    <li>Lorem ipsum dolor sit amet, consectetur adipiscing elit</li>
  </ul>
</section>
<div class="num" style="left:804px;top:709px;">3</div>

<!-- 10 Biographies -->
<section class="slide" style="left:11px;top:730px;">
  <div class="band"></div>
  <div class="band-title" style="top:44px;">HEADING <span class="light">FOR</span><br>BIOGRAPHIES</div>
  <div class="brand brand-light"><span class="dot"></span><div class="w1">HOLLOWAY</div><div class="w2">ENGINES</div></div>
  <div class="name" style="left:48px;top:138px;">NAME NAME</div>
  <div class="role" style="left:48px;top:158px;width:146px;">TITLE TITLE TITLE TITLE</div>
  <div class="bio" style="left:48px;top:182px;width:150px;">Lorem ipsum dolor sit amet, consectetur adipiscing elit. V orem ipsum dolor sit amet, consectetur adipiscing elit. V estibulum lacinia eros eu pharetra mollis. Nullam vulputate purus mi, sed maximurisus. Nunc pharetra</div>
  <div class="photo" role="img" aria-label="Portrait photo placeholder" style="left:212px;top:148px;"></div>
  <div class="divider" style="left:304px;top:134px;height:150px;"></div>
  <div class="photo" role="img" aria-label="Portrait photo placeholder" style="left:320px;top:148px;"></div>
  <div class="name" style="left:414px;top:138px;width:146px;text-align:right;">NAME NAME</div>
  <div class="role" style="left:414px;top:158px;width:146px;text-align:right;">TITLE TITLE TITLE TITLE</div>
  <div class="bio" style="left:410px;top:182px;width:150px;text-align:right;">Lorem ipsum dolor sit amet, consectetur adipiscing elit. V orem ipsum dolor sit amet, consectetur adipiscing elit. V estibulum lacinia eros eu pharetra mollis. Nullam vulputate purus mi, sed maximurisus. Nunc pharetra</div>
</section>
<div class="num" style="left:11px;top:945px;">10</div>

<!-- 7 Table -->
<section class="slide" style="left:408px;top:730px;">
  <div class="band"></div>
  <div class="band-title">ANOTHER<br>SECTION TITLE</div>
  <div class="band-sub">Another Subsection Title</div>
  <div class="brand brand-light"><span class="dot"></span><div class="w1">HOLLOWAY</div><div class="w2">ENGINES</div></div>
  <table class="data-table">
    <thead><tr><th>PURCHASE<br>TIME</th><th>SALES<br>ID</th><th>COSTUMER<br>ID</th><th>CURRENCY</th><th>AMOUNT<br>PAID</th><th>DEVICE</th><th>DISC<br>%</th><th>AGENT<br>COMMENT</th></tr></thead>
    <tbody>
      <tr><td>2018/01/01 · 08.48</td><td>466</td><td>1234</td><td>USD</td><td>$ 98.23</td><td>mobile app</td><td>FALSE</td><td></td></tr>
      <tr><td>2018/01/01 · 09.15</td><td>467</td><td>3485</td><td>USD</td><td>$ 34.35</td><td>desktop</td><td>FALSE</td><td>out of stock in blue<br>accepted switch to<br>green for a 5% disc</td></tr>
      <tr><td>2018/01/01 · 15.12</td><td>468</td><td>875</td><td>USD</td><td>$ 34.35</td><td>mobile web</td><td>FALSE</td><td></td></tr>
      <tr><td>2018/01/01 · 16.48</td><td>469</td><td>875</td><td>USD</td><td>$ 34.35</td><td>desktop</td><td>FALSE</td><td></td></tr>
      <tr><td>2018/01/01 · 18.09</td><td>470</td><td>5246</td><td>USD</td><td>$ 34.35</td><td>mobile web</td><td>FALSE</td><td></td></tr>
      <tr><td>2018/01/01 · 18.33</td><td>471</td><td>9872</td><td>USD</td><td>$ 34.35</td><td>mobile web</td><td>FALSE</td><td></td></tr>
      <tr><td>2018/01/01 · 07.25</td><td>472</td><td>2498</td><td>USD</td><td>$ 34.35</td><td>desktop</td><td>FALSE</td><td></td></tr>
      <tr><td>2018/01/01 · 08.01</td><td>473</td><td>7892</td><td>USD</td><td>$ 34.35</td><td>desktop</td><td>FALSE</td><td></td></tr>
    </tbody>
  </table>
  <div class="footnote" style="left:48px;top:298px;"><b>FOOTNOTE:</b>Data shown net of fees and based on monthly returns since inception; past performance is not indicative of future results and may vary.</div>
  <div class="h-body" style="left:398px;top:138px;">TABLE <span class="light">WITH</span><br>A FOOTNOTE</div>
  <ul class="bullets" style="left:398px;top:180px;width:190px;">
    <li>Lorem ipsum dolor sit amet, consectetur adipiscing elit</li>
    <li>Lorem ipsum dolor sit amet, consectetur adipiscing elit</li>
    <li>Lorem ipsum dolor sit amet, consectetur adipiscing elit</li>
  </ul>
</section>
<div class="num" style="left:408px;top:945px;">7</div>

<!-- 4 Bar chart -->
<section class="slide" style="left:804px;top:730px;">
  <div class="band"></div>
  <div class="band-title">ANOTHER<br>SECTION TITLE</div>
  <div class="band-sub">Subsection With A Footnote*</div>
  <div class="brand brand-light"><span class="dot"></span><div class="w1">HOLLOWAY</div><div class="w2">ENGINES</div></div>
  <div class="footnote" style="left:48px;top:286px;width:36px;font-size:4px;">Source: Internal Data 2019</div>
  <svg style="left:84px;top:140px;" width="170" height="185" viewBox="0 0 170 185" role="img" aria-label="Bar chart rising from 22 to 93 percent">
    <g fill="var(--navy)">
      <rect x="2"   y="144" width="18" height="38"/>
      <rect x="26"  y="121" width="18" height="61"/>
      <rect x="50"  y="84"  width="18" height="98"/>
      <rect x="74"  y="67"  width="18" height="115"/>
      <rect x="98"  y="51"  width="18" height="131"/>
      <rect x="122" y="33"  width="18" height="149"/>
      <rect x="146" y="19"  width="18" height="163"/>
    </g>
    <line x1="0" y1="182.5" x2="168" y2="182.5" stroke="var(--navy)" stroke-width="1"/>
    <g class="bar-label" font-family="Roboto, sans-serif" font-weight="700" font-size="8" fill="var(--navy)" text-anchor="middle">
      <text x="11" y="140">22%</text><text x="35" y="117">35%</text><text x="59" y="80">56%</text>
      <text x="83" y="63">66%</text><text x="107" y="47">75%</text><text x="131" y="29">85%</text><text x="155" y="15">93%</text>
    </g>
  </svg>
  <div class="h-body" style="left:274px;top:148px;">TITLE <span class="light">OF</span> BARCHART</div>
  <ul class="bullets" style="left:274px;top:172px;width:200px;">
    <li>Lorem ipsum dolor sit amet, consectetur adipiscing elit</li>
    <li>Lorem ipsum dolor sit amet, consectetur adipiscing elit</li>
    <li>Lorem ipsum dolor sit amet, consectetur adipiscing elit</li>
  </ul>
  <div class="footnote" style="left:274px;top:300px;width:290px;"><b>FOOTNOTE:</b>Data shown net of fees and based on monthly returns since inception; past performance is not indicative of future results and may vary.</div>
</section>
<div class="num" style="left:804px;top:945px;">4</div>

<!-- 11 Closing -->
<section class="slide full-blue" style="left:11px;top:967px;">
  <div class="brand" style="color:#fff;left:184px;top:120px;width:240px;">
    <span class="dot" style="background:#fff;width:14px;height:14px;margin-bottom:8px;"></span>
    <div class="w1" style="font-size:32px;">HOLLOWAY</div>
    <div class="w2" style="font-size:15px;letter-spacing:10px;padding-left:10px;margin-top:5px;">ENGINES</div>
  </div>
</section>
<div class="num" style="left:11px;top:1182px;">11</div>

<!-- 8 Line chart -->
<section class="slide" style="left:408px;top:967px;">
  <div class="band"></div>
  <div class="band-title">ANOTHER<br>SECTION TITLE</div>
  <div class="band-sub">Another Subsection Title</div>
  <div class="brand brand-light"><span class="dot"></span><div class="w1">HOLLOWAY</div><div class="w2">ENGINES</div></div>
  <div class="h-body" style="left:20px;top:218px;width:98px;text-align:right;font-size:16px;">CHART<br>TITLE</div>
  <div class="body-copy" style="left:20px;top:252px;width:98px;text-align:right;font-size:10px;">with a Second<br>Footnote</div>
  <svg style="left:128px;top:118px;" width="262" height="165" viewBox="0 0 262 165" role="img" aria-label="Line chart rising from 2010 to 2020">
    <g font-family="Roboto, sans-serif" font-size="4" fill="#555" text-anchor="end">
      <text x="22" y="8">6,E+07</text><text x="22" y="24">5,5E+07</text><text x="22" y="40">5,E+07</text>
      <text x="22" y="56">4,5E+07</text><text x="22" y="72">4,E+07</text><text x="22" y="88">3,5E+07</text>
      <text x="22" y="104">3,E+07</text><text x="22" y="120">2,5E+07</text><text x="22" y="136">2,E+07</text><text x="22" y="152">1,E+07</text>
    </g>
    <g stroke="#dcdcdc" stroke-width=".5">
      <line x1="26" y1="6" x2="258" y2="6"/><line x1="26" y1="38" x2="258" y2="38"/><line x1="26" y1="70" x2="258" y2="70"/>
      <line x1="26" y1="102" x2="258" y2="102"/><line x1="26" y1="134" x2="258" y2="134"/>
    </g>
    <line x1="26" y1="152" x2="258" y2="152" stroke="#888" stroke-width=".6"/>
    <g font-family="Roboto, sans-serif" font-size="4.5" fill="#555" text-anchor="middle">
      <text x="28" y="160">2010</text><text x="92" y="160">2013</text><text x="156" y="160">2016</text><text x="220" y="160">2019</text>
    </g>
    <polyline fill="none" stroke="#9fc8a8" stroke-width="2.4"
      points="28,146 38,140 46,134 56,126 64,122 72,114 80,108 90,104 98,98 108,94 116,90 126,84 134,80 144,76 152,70 160,66 170,62 178,54 186,50 196,42 204,38 214,32 224,28 234,22 242,20 250,16 256,14"/>
    <polyline fill="none" stroke="var(--navy)" stroke-width=".9"
      points="28,147 34,143 40,141 46,135 52,131 58,127 64,123 70,117 76,112 82,109 88,106 94,101 100,99 106,95 112,93 118,89 124,86 130,82 136,81 142,77 148,73 154,70 160,68 166,64 172,61 178,55 184,52 190,47 196,44 202,39 208,37 214,33 220,30 226,28 232,24 238,22 244,20 250,17 256,15"/>
  </svg>
  <div class="h-body" style="left:398px;top:120px;font-size:17px;"><span class="light">HEADING</span><br>HEADING</div>
  <div class="body-copy" style="left:398px;top:156px;width:180px;font-size:11px;">A description of the chart with a footnote*</div>
  <div class="h-body" style="left:398px;top:196px;font-size:17px;"><span class="light">SECOND</span><br>HEADING</div>
  <div class="body-copy" style="left:398px;top:232px;width:180px;font-size:11px;">Another description of the chart with the same footnote*</div>
  <div class="footnote" style="left:48px;top:300px;width:400px;"><b>FOOTNOTE:</b>Data shown net of fees and based on monthly returns since inception; past performance is not indicative of future results and may vary.</div>
</section>
<div class="num" style="left:408px;top:1182px;">8</div>

<!-- 5 Section two -->
<section class="slide" style="left:804px;top:967px;">
  <div class="brand brand-dark"><span class="dot"></span><div class="w1">HOLLOWAY</div><div class="w2">ENGINES</div></div>
  <div class="sec-num">02</div>
  <div class="sec-title" style="left:190px;">SECTION<br>TWO<br>TITLE</div>
</section>
<div class="num" style="left:804px;top:1182px;">5</div>

</body>
</html>
```